eCommerce website for a DIY shop & communal center

We need a website for a business called The Maple Bench. The Maple Bench is both a shop and communal establishment where people with shared interests, especially in DIY (Do It Yourself) and crafting, can gather to shop for & work on projects while sharing ideas, equipment, supplies and knowledge. The shop is both brick & motor and online. The physical communal space provides workstations, equipment, tools and supplies and expertise for DIY lovers to create their projects.

Target Market(s)

Middle & upper class DIY enthusiasts, creative hobbyists, budding artists & small business owners

Industry/Entity Type

DIY, Arts & Crafts

Coding

Coded - Design and coding required

Number of Pages Required

5+ page

Requirements
Must have
• Menus to include 1. home page (with about us, operating hours, contacts, location, meet the team); 2. Bench activities (how to DIY at the Bench, booking, equipment & tools, house rules); 3. Bench events (events in the Bench, offsite events); 4. Resources (FAQs, tutorials, blogs, eBooks) and 5. Online shop
Nice to have
• Branding guidelines eg logo colours (see attachment) to influence design. Tillpost shop. Booking feature for activities & events at the Bench.

```html
<!DOCTYPE html>
<html lang="en">
<head>
<meta charset="utf-8">
<title>DIY Bench</title>
<link href="https://fonts.googleapis.com/css2?family=Oswald:wght@400;500;600&family=Roboto:wght@400;500;700&display=swap" rel="stylesheet">
<style>
:root{
  --blue:#1565c0;
  --blue-dark:#0d4ea0;
  --ink:#111;
  --text:#555;
  --line:#e2e2e2;
  --white:#fff;
  --footer:#0b0b0b;
  --footer-bottom:#1a1a1a;
}
*{box-sizing:border-box;margin:0;padding:0}
html,body{width:1200px;height:3416px;overflow:hidden}
body{position:relative;font-family:'Roboto',sans-serif;color:var(--ink);background:var(--white)}
.abs{position:absolute}
h1,h2,h3,.logo,.caption{font-family:'Oswald',sans-serif}
.topbar{left:0;top:0;width:1200px;height:32px;background:var(--blue);color:var(--white);font-size:13px;text-align:center;line-height:32px}
.header{left:0;top:32px;width:1200px;height:80px;background:var(--white)}
.logo{font-weight:600;font-size:40px;line-height:1}
.header .logo{left:112px;top:18px}
.nav{right:112px;top:30px;display:flex;gap:38px;align-items:center;font-size:15px}
.hero{left:0;top:112px;width:1200px;height:600px;background:radial-gradient(ellipse at center,#1b1b1b 0%,#1b1b1b 45%,#7a3f6e 70%,#c8852c 85%,#2f7bc4 100%)}
.hero-text{left:0;top:160px;width:1200px;text-align:center;color:var(--white)}
.hero h1{font-family:'Roboto',sans-serif;font-weight:500;font-size:84px;line-height:1}
.hero p{font-size:22px;line-height:30px;margin:18px auto 0;width:520px}
.btn{display:inline-block;background:var(--blue);color:var(--white);font-size:13px;font-weight:500;padding:14px 28px;letter-spacing:.5px}
.hero .btn{margin-top:30px}
.about-photo{left:140px;top:792px;width:440px;height:388px;background:linear-gradient(135deg,#d9d2c8,#b9a58e 55%,#8c6e5a)}
.about-text{left:648px;top:824px;width:420px}
h2{font-weight:500;font-size:48px;line-height:1}
h2 b{font-weight:600}
.about-text p{font-size:15px;line-height:25px;color:var(--text);margin-top:22px}
.about-text .btn{margin-top:26px}
.products{left:0;top:1260px;width:1200px;height:520px;background:linear-gradient(120deg,var(--blue-dark),var(--blue) 50%,#1e74d0)}
.products h2{color:var(--white);text-align:center;position:absolute;top:80px;width:100%}
.product{top:140px;width:236px}
.product .photo{height:260px}
.caption{color:var(--white);font-size:20px;text-align:center;margin-top:26px}
.team h2{text-align:center;position:absolute;top:1860px;left:0;width:1200px}
.card{width:480px;height:216px;border:1px solid var(--line);box-shadow:0 2px 6px rgba(0,0,0,.08);background:var(--white)}
.card .portrait{position:absolute;left:16px;top:16px;width:180px;height:184px;background:linear-gradient(160deg,#cfd8e3,#8aa3bd)}
.card .info{position:absolute;left:212px;top:18px;width:250px}
.card h3{font-size:28px;font-weight:500;line-height:1}
.card .role{font-size:15px;color:var(--text);margin-top:8px}
.card p{font-size:12px;line-height:18px;color:var(--text);margin-top:10px}
.icons{display:flex;gap:12px;margin-top:10px}
.icons span{width:14px;height:14px;border-radius:50%;background:var(--blue)}
.contact{left:0;top:2460px;width:1200px;height:580px;background:linear-gradient(120deg,var(--blue-dark),var(--blue) 50%,#1e74d0)}
.contact h2{color:var(--white);text-align:center;position:absolute;top:100px;width:100%}
.field{background:var(--white);font-size:14px;color:#444;padding:14px 12px;height:50px}
.submit{left:500px;top:2908px;width:200px;height:44px;border:2px solid var(--white);border-radius:22px;color:var(--white);font-weight:700;font-size:13px;text-align:center;line-height:40px}
.footer{left:0;top:3040px;width:1200px;height:332px;background:var(--footer);color:var(--white)}
.footer .logo{left:112px;top:64px;font-size:52px}
.social{left:124px;top:156px;display:flex;gap:12px}
.social span{width:28px;height:28px;border-radius:50%;background:var(--blue)}
.col h4{font-family:'Oswald',sans-serif;font-weight:500;font-size:17px;letter-spacing:.5px}
.col h4::after{content:"";display:block;width:40px;height:2px;background:var(--white);margin-top:8px}
.hours{margin-top:18px;font-size:14px;line-height:26px}
.hours td{padding-right:40px}
.cline{display:flex;gap:14px;align-items:center;font-size:14px;line-height:20px;margin-top:16px}
.cline .dot{width:30px;height:30px;border-radius:50%;background:var(--white);flex:none;display:flex;align-items:center;justify-content:center}
.map{margin-top:20px;width:200px;height:120px;background:linear-gradient(135deg,#e8e6e1,#d3d7cf)}
.bottom{left:0;top:3372px;width:1200px;height:44px;background:var(--footer-bottom);color:#ccc;font-size:13px;text-align:center;line-height:44px}
</style>
</head>
<body>
<div class="abs topbar">Covid 19 Updates - De Finibus Bonorum et Malorum! | written by Ada Lorne</div>

<header class="abs header">
  <div class="abs logo">DIY Bench</div>
  <nav class="abs nav">
    <span>Home</span><span>Bench Activities</span><span>Bench Events</span><span>Resources</span><span>Online Shop</span>
    <svg width="26" height="26" viewBox="0 0 24 24" fill="none" stroke="#1565c0" stroke-width="2"><path d="M6 8h12l-1 12H7z"/><path d="M9 8a3 3 0 0 1 6 0"/></svg>
  </nav>
</header>

<section class="abs hero" role="img" aria-label="Craft supplies arranged around a dark board: yarn, buttons, threads, scissors and beads">
  <div class="abs hero-text">
    <h1>DIY Bench</h1>
    <p>Lorem ipsum dolor sit amet, conse adipiscing elit, sed do eiusmod tempor incididunt</p>
    <span class="btn">GET STARTED</span>
  </div>
</section>

<div class="abs about-photo" role="img" aria-label="Hands working on a craft project at a table with scissors and glue gun"></div>
<section class="abs about-text">
  <h2><b>ABOUT</b> Us</h2>
  <p>Lorem ipsum dolor sit amet, consectetur adipiscing, sed do eiusmod tempor incididunt ut labore ets magna aliqu. Quis ipsum suspendisse ultrices gravida. Risi commodo viverra maecenas accumsan lacus vel facilisi. Lorem ipsum dolor sit amet, consectetur adipiscing, sed do eiusmod tempor incididunt ut labore ets magna aliqu. Quis ipsum suspendisse ultrices gravida. Risi commodo viverra maecenas accumsan lacus vel facilisis.</p>
  <span class="btn">LEARN MORE</span>
</section>

<section class="abs products">
  <h2><b>OUR</b> Products</h2>
  <div class="abs product" style="left:112px"><div class="photo" role="img" aria-label="Knitting with green yarn" style="background:linear-gradient(160deg,#6d8a5a,#c7c2b5)"></div><div class="caption">De Finibus Bonorum et</div></div>
  <div class="abs product" style="left:360px"><div class="photo" role="img" aria-label="Colourful craft materials on a table" style="background:linear-gradient(160deg,#c9a07a,#6f9bb8)"></div><div class="caption">De Finibus Bonorum et</div></div>
  <div class="abs product" style="left:608px"><div class="photo" role="img" aria-label="Handmade cream in a jar" style="background:linear-gradient(160deg,#3d4a3a,#e8e2d6 60%,#2c2c2c)"></div><div class="caption">De Finibus Bonorum et</div></div>
  <div class="abs product" style="left:852px"><div class="photo" role="img" aria-label="Handmade jewellery on display" style="background:linear-gradient(160deg,#1d2330,#3a4256)"></div><div class="caption">De Finibus Bonorum et</div></div>
</section>

<section class="team">
  <h2><b>MEET THE</b> Team</h2>
  <div class="abs card" style="left:112px;top:1932px"><div class="portrait" role="img" aria-label="Team member portrait"></div><div class="info"><h3>JOHN SMITH</h3><div class="role">Finibus Bonorum et</div><p>Lorem ipsum dolor sit amet, consetur adipiscing elit, sed do eiusmod tempor incididunt ut labore et dolore magna aliqua.</p><div class="icons"><span></span><span></span><span></span></div></div></div>
  <div class="abs card" style="left:608px;top:1932px"><div class="portrait" role="img" aria-label="Team member portrait"></div><div class="info"><h3>JOHN SMITH</h3><div class="role">Finibus Bonorum et</div><p>Lorem ipsum dolor sit amet, consetur adipiscing elit, sed do eiusmod tempor incididunt ut labore et dolore magna aliqua.</p><div class="icons"><span></span><span></span><span></span></div></div></div>
  <div class="abs card" style="left:112px;top:2164px"><div class="portrait" role="img" aria-label="Team member portrait"></div><div class="info"><h3>JOHN SMITH</h3><div class="role">Finibus Bonorum et</div><p>Lorem ipsum dolor sit amet, consetur adipiscing elit, sed do eiusmod tempor incididunt ut labore et dolore magna aliqua.</p><div class="icons"><span></span><span></span><span></span></div></div></div>
  <div class="abs card" style="left:608px;top:2164px"><div class="portrait" role="img" aria-label="Team member portrait"></div><div class="info"><h3>JOHN SMITH</h3><div class="role">Finibus Bonorum et</div><p>Lorem ipsum dolor sit amet, consetur adipiscing elit, sed do eiusmod tempor incididunt ut labore et dolore magna aliqua.</p><div class="icons"><span></span><span></span><span></span></div></div></div>
</section>

<section class="abs contact">
  <h2><b>GET IN</b> Touch</h2>
</section>
<div class="abs field" style="left:208px;top:2636px;width:384px">First Name</div>
<div class="abs field" style="left:608px;top:2636px;width:384px">Last Name</div>
<div class="abs field" style="left:208px;top:2704px;width:384px">Email</div>
<div class="abs field" style="left:608px;top:2704px;width:384px">Phone</div>
<div class="abs field" style="left:208px;top:2772px;width:784px;height:110px">How Can We Help?</div>
<div class="abs submit">SUBMIT</div>

<footer class="abs footer">
  <div class="abs logo">DIY Bench</div>
  <div class="abs social"><span></span><span></span><span></span><span></span></div>
  <div class="abs col" style="left:368px;top:48px">
    <h4>OPERATING HOURS</h4>
    <table class="hours">
      <tr><td>Monday</td><td>9am to 8Pm</td></tr>
      <tr><td>Tuesday</td><td>9am to 8Pm</td></tr>
      <tr><td>Wednesday</td><td>9am to 8Pm</td></tr>
      <tr><td>Thursday</td><td>9am to 8Pm</td></tr>
      <tr><td>Friday</td><td>9am to 8Pm</td></tr>
      <tr><td>Saturday</td><td>9am to 8Pm</td></tr>
      <tr><td>Sunday</td><td>Closed</td></tr>
    </table>
  </div>
  <div class="abs col" style="left:612px;top:48px">
    <h4>CONTACT DETAILS</h4>
    <div class="cline"><span class="dot"><svg width="14" height="14" viewBox="0 0 24 24" fill="#0b0b0b"><path d="M12 2a7 7 0 0 0-7 7c0 5 7 13 7 13s7-8 7-13a7 7 0 0 0-7-7zm0 9.5A2.5 2.5 0 1 1 12 6a2.5 2.5 0 0 1 0 5.5z"/></svg></span><span>48 Alder Row<br>Fenwick, 20931</span></div>
    <div class="cline"><span class="dot"><svg width="14" height="14" viewBox="0 0 24 24" fill="#0b0b0b"><path d="M6.6 10.8a15 15 0 0 0 6.6 6.6l2.2-2.2a1 1 0 0 1 1-.25 11 11 0 0 0 3.6.6 1 1 0 0 1 1 1V20a1 1 0 0 1-1 1A17 17 0 0 1 3 4a1 1 0 0 1 1-1h3.5a1 1 0 0 1 1 1 11 11 0 0 0 .6 3.6 1 1 0 0 1-.25 1z"/></svg></span><span>(000) 000 - 0000</span></div>
    <div class="cline"><span class="dot"><svg width="14" height="14" viewBox="0 0 24 24" fill="none" stroke="#0b0b0b" stroke-width="2"><rect x="3" y="5" width="18" height="14"/><path d="M3 6l9 7 9-7"/></svg></span><span>hello@maplebench.shop</span></div>
  </div>
  <div class="abs col" style="left:880px;top:48px">
    <h4>LOCATION MAP</h4>
    <div class="map" role="img" aria-label="Street map showing the bench location"></div>
  </div>
</footer>
<div class="abs bottom">© 2021 DIY Bench All Rights Reserved</div>
</body>
</html>
```